Custom PowerPoint Template for Training & Workshop Presentations

I am looking for a professional designer to create a custom PowerPoint template (PPTX) for my training and workshop materials. My trainings are designed for: HR professionals and Learning & Development specialists;
Executives and team leaders; Organizations investing in employee development and workplace learning; Participants in professional development workshops, seminars, and didactics trainings
The template should therefore appear trustworthy, calm, friendly, structured, and competence‑oriented. The design should be visually appealing, easy to read, and fully editable.

All branding files are attached to this project.
Please use them as the main reference for your design:
Logo (included as attachment)
Brand color specifications (included as attachment)
Font specifications related to the logo and brand (included as attachment)

What I need:
--> Title Slide: Title, subtitle, name, logo
(1–2 variations)
--> Agenda / Overview Slide
--> Content Slides
--> Text only
--> Text + image
-->Two-column
--> Section header
--> Quote / key message
--> Graphic / Model Slides: (1–2 layouts for frameworks, processes, models)
--> Tables & Charts: (Table styles in brand colors; Chart design aligned with typography and color palette)
--> Closing Slide: (Contact or call-to-action; Optional second variation)

All layouts must be built properly inside the PowerPoint Slide Master

```html
<!DOCTYPE html>
<html lang="en">
<head>
<meta charset="utf-8">
<title>Training Template – Slide Overview</title>
<link rel="stylesheet" href="https://fonts.googleapis.com/css2?family=Archivo:wght@600;800&family=Inter:wght@400;500;600;700&display=swap">
<style>
:root{
  --board:#3b393a;
  --navy:#1a4a85;
  --navy-deep:#143c6e;
  --steel:#7596b8;
  --steel-light:#a9bdd3;
  --tint:#eef3f9;
  --white:#ffffff;
  --ink:#1c1c1c;
  --text:#555a60;
}
*{box-sizing:border-box;margin:0;padding:0}
html,body{width:990px;height:1200px;overflow:hidden;background:var(--board)}
body{position:relative;font-family:"Inter",sans-serif;color:var(--text)}
.slide{position:absolute;width:440px;height:247px;background:var(--white);overflow:hidden;border-bottom:1px solid var(--steel-light)}
.col-a{left:38px}.col-b{left:513px}
.row-1{top:55px}.row-2{top:336px}.row-3{top:617px}.row-4{top:898px}

.header-band{position:absolute;left:0;top:11px;width:268px;height:27px;background:var(--navy);border-radius:0 14px 14px 0;display:flex;align-items:center;padding-left:22px}
.header-band .dot{width:12px;height:12px;border:1.3px solid var(--white);border-radius:50%;margin-right:14px}
.header-band h2{font-family:"Archivo",sans-serif;font-weight:800;font-size:12.5px;color:var(--white);letter-spacing:.2px}

.footer-date{position:absolute;left:23px;bottom:8px;font-size:4.6px;font-weight:700;color:var(--navy);letter-spacing:.2px}
.brand{position:absolute;right:23px;bottom:8px;display:flex;align-items:center;gap:4px}
.brand .mark{width:9px;height:9px;border:1px solid var(--navy);border-radius:50%}
.brand span{font-family:"Inter",sans-serif;font-weight:600;font-size:6.6px;color:var(--navy)}

p,li{font-size:6.3px;line-height:12.4px}

/* title slide */
.hero-photo{position:absolute;inset:0;background:linear-gradient(110deg,#6f6a66 0%,#8b8480 28%,#4b4f57 55%,#2d3544 100%)}
.hero-wave{position:absolute;left:0;bottom:0;width:440px;height:90px}
.hero-badge{position:absolute;left:40px;top:152px;width:88px;height:88px;border-radius:50%;background:linear-gradient(150deg,#2c5f9c,#1a4a85)}
.hero-brand{position:absolute;left:244px;top:27px;display:flex;align-items:center;gap:5px}
.hero-brand .mark{width:14px;height:14px;border:1.3px solid var(--white);border-radius:50%}
.hero-brand span{font-weight:600;font-size:11.5px;color:var(--white)}
.title-box{position:absolute;left:244px;background:var(--white);border-radius:4px;font-family:"Archivo",sans-serif;font-weight:800;color:var(--navy);display:flex;align-items:center;padding:0 7px}
.title-box.one{top:66px;height:33px;font-size:18.5px}
.title-box.two{top:104px;height:33px;font-size:24px}
.hero-sub{position:absolute;left:244px;top:143px;font-family:"Archivo",sans-serif;font-weight:600;font-size:12px;line-height:17px;color:var(--white)}
.hero-by{position:absolute;left:244px;top:183px;font-size:6.6px;color:var(--white)}

/* learning objectives */
.obj-left{position:absolute;left:23px;top:53px;width:186px}
.obj-right{position:absolute;left:232px;top:53px;width:190px}
.obj-left p{text-align:justify}
.ticks{list-style:none}
.ticks li{position:relative;padding-left:13px}
.ticks li::before{content:"";position:absolute;left:0;top:3.5px;width:5.5px;height:5.5px;border-radius:50%;background:#2140a8}
.label{color:var(--ink);font-weight:600}

/* TOC */
.toc{position:absolute;left:141px;top:58px;list-style:none}
.toc li{display:flex;font-size:7.3px;line-height:21.1px;color:var(--text)}
.toc b{width:29px;color:var(--ink);font-weight:600}

/* table */
.serve-table{position:absolute;left:48px;top:56px;width:344px;border-collapse:collapse;border-radius:8px;overflow:hidden;box-shadow:0 2px 8px rgba(26,74,133,.16)}
.serve-table th{font-family:"Archivo",sans-serif;font-weight:700;font-size:8.4px;color:var(--white);text-align:left;height:24px;padding-left:18px}
.serve-table th.aud{background:var(--steel);width:123px}
.serve-table th.need{background:var(--navy)}
.serve-table td{height:33px;font-size:5.8px;vertical-align:middle;padding-left:18px}
.serve-table td.aud{font-weight:700;color:var(--ink);border-right:1px solid #dfe6ef}
.serve-table td.need{font-size:5.4px;line-height:10.5px;color:var(--text);padding-right:16px}
.serve-table tr.shade td{background:var(--tint)}

/* workshop description */
.desc-head{position:absolute;left:0;right:0;top:54px;text-align:center;font-size:6.8px;line-height:12px;font-weight:600;color:var(--ink)}
.desc-body{position:absolute;left:64px;right:64px;top:88px;text-align:center}
.desc-body p+p{margin-top:12px}

/* working process */
.proc-text{position:absolute;left:23px;top:60px;width:188px}
.proc-text .lead{font-size:5.7px;line-height:10.3px;font-weight:600;color:var(--ink)}
.proc-text p{font-size:5.6px;line-height:10.8px;text-align:justify}
.proc-text p+p{margin-top:10px}
.bars{position:absolute;left:231px;top:60px;width:176px;list-style:none}
.bars li{position:relative;height:13.5px;margin-bottom:7.8px;border-radius:7px;background:var(--white);box-shadow:0 1px 5px rgba(26,74,133,.14)}
.bars .fill{position:absolute;left:0;top:0;bottom:0;border-radius:7px}
.bars .light{background:var(--steel)}
.bars .dark{background:var(--navy)}
.bars em{position:absolute;right:8px;top:0;line-height:13.5px;font-style:normal;font-size:4.2px;font-weight:600;color:var(--ink)}

/* about */
.about-text{position:absolute;left:23px;top:58px;width:187px}
.about-text p{text-align:justify;font-size:6.3px;line-height:12.8px}
.about-text p+p{margin-top:12px}
.sig{position:absolute;left:31px;top:174px;border-left:1.5px solid var(--navy);padding-left:11px}
.sig strong{display:block;font-size:6.3px;font-weight:700;color:var(--navy);line-height:11px}
.sig span{font-size:6px;color:var(--navy)}
.portrait{position:absolute;left:238px;top:43px;width:160px;height:160px;border-radius:50%;background:linear-gradient(135deg,#8fa4a8,#4e6c6f 55%,#c7d2d3);box-shadow:0 0 18px 6px rgba(117,150,184,.22)}

/* closing */
.close-photo{position:absolute;inset:0;background:linear-gradient(120deg,#9aa1a6 0%,#6b7177 40%,#4a5158 70%,#7c8287 100%)}
.close-wave{position:absolute;left:0;bottom:0;width:440px;height:120px}
.close-ring{position:absolute;left:42px;top:169px;width:66px;height:66px;border:3px solid var(--white);border-radius:50%}
.close-kicker{position:absolute;left:142px;top:184px;font-family:"Archivo",sans-serif;font-weight:700;font-size:10px;color:var(--white)}
.close-title{position:absolute;left:142px;top:198px;font-family:"Archivo",sans-serif;font-weight:800;font-size:14.5px;line-height:21px;color:var(--white)}
</style>
</head>
<body>

<!-- Title slide -->
<section class="slide col-a row-1">
  <div class="hero-photo" role="img" aria-label="Photo of a trainer presenting to a seated workshop audience"></div>
  <svg class="hero-wave" viewBox="0 0 440 90" preserveAspectRatio="none" aria-hidden="true">
    <path d="M0 90 L0 60 C90 18 200 20 300 40 C360 52 410 52 440 36 L440 90 Z" fill="#1a4a85"/>
    <path d="M0 90 L0 72 C90 34 200 36 300 56 C360 68 410 70 440 60 L440 90 Z" fill="#ffffff"/>
  </svg>
  <div class="hero-badge"></div>
  <div class="hero-brand"><div class="mark"></div><span>Dr. Lena Hartwig-Brandt</span></div>
  <div class="title-box one">DEVELOPING</div>
  <div class="title-box two">SKILLS FOR</div>
  <div class="hero-sub">Effective Leadership<br>&amp; Workplace Learning</div>
  <div class="hero-by">By Mara Lindqvist</div>
</section>

<!-- Learning objectives -->
<section class="slide col-b row-1">
  <header class="header-band"><div class="dot"></div><h2>LEARNING OBJECTIVES</h2></header>
  <div class="obj-left">
    <p>The workshop combines short presentations by the trainer with individual reflection and small group work. It is aimed at teachers who want to strengthen their mental resilience and gain new perspectives. Key components that participants should bring to the workshop are the ability to reflect and a willingness to change.</p>
    <p style="margin-top:12px">Competency-oriented learning objectives:<br><span class="label">After the workshop you will be able to:</span></p>
    <ul class="ticks" style="margin-top:6px">
      <li>Identify the seven resilience factors and derive possibilities for strengthening them.</li>
      <li style="margin-top:2px">Assess and reflect on your personal resilience.</li>
    </ul>
  </div>
  <div class="obj-right">
    <ul class="ticks">
      <li>Identify stressors, stress amplifiers and stress reactions in everyday teaching.</li>
      <li>Use ideas for further individual work on your resilience.</li>
    </ul>
    <p class="label" style="margin-top:10px">Duration:</p>
    <p style="margin-top:10px">The seminar can be conducted as a one-day or 1.5-day event (e.g., a one-day seminar followed by a follow-up session). Individual adjustments and follow-up formats are possible. Resilience cannot be developed through mere input. For this reason, I do not offer short lectures , but rather practice-oriented workshops with a strong emphasis on reflection.</p>
  </div>
  <div class="footer-date">05 &nbsp;|&nbsp; DATE: 11/01/2026</div>
  <div class="brand"><div class="mark"></div><span>Dr. Lena Hartwig-Brandt</span></div>
</section>

<!-- Table of contents -->
<section class="slide col-a row-2">
  <header class="header-band"><div class="dot"></div><h2>TABLE OF CONTENTS</h2></header>
  <ol class="toc">
    <li><b>01</b>Introduction</li>
    <li><b>02</b>Table Of Contents (Agenda)</li>
    <li><b>03</b>Workshop description</li>
    <li><b>04</b>About Dr. phil. Lena Hartwig-Brandt, MBA</li>
    <li><b>05</b>Competency-oriented learning objectives</li>
    <li><b>06</b>Real-World Leadership Experience</li>
    <li><b>07</b>Who We Partner With</li>
    <li><b>08</b>Thank You</li>
  </ol>
  <div class="footer-date">02 &nbsp;|&nbsp; DATE: 11/01/2026</div>
  <div class="brand"><div class="mark"></div><span>Dr. Lena Hartwig-Brandt</span></div>
</section>

<!-- Who we serve -->
<section class="slide col-b row-2">
  <header class="header-band"><div class="dot"></div><h2>WHO WE SERVE</h2></header>
  <table class="serve-table">
    <thead><tr><th class="aud">AUDIENCE</th><th class="need">NEEDS ADDRESSED</th></tr></thead>
    <tbody>
      <tr class="shade"><td class="aud">EXECUTIVES</td><td class="need">Ut enim ad minima veniam, quis nostrum exercitationem ullam corporis suscipit laboriosam, nisi ut aliquid ex ea</td></tr>
      <tr><td class="aud">GROWING ORGANIZATIONS</td><td class="need">Ut enim ad minima veniam, quis nostrum exercitationem ullam corporis suscipit laboriosam, nisi ut aliquid ex ea</td></tr>
      <tr class="shade"><td class="aud">TRANSITIONING COMPANIES</td><td class="need">Ut enim ad minima veniam, quis nostrum exercitationem ullam corporis suscipit laboriosam, nisi ut aliquid ex ea</td></tr>
      <tr><td class="aud">EMERGING LEADERS</td><td class="need">Ut enim ad minima veniam, quis nostrum exercitationem ullam corporis suscipit laboriosam, nisi ut aliquid ex ea</td></tr>
    </tbody>
  </table>
  <div class="footer-date">06 &nbsp;|&nbsp; DATE: 11/01/2026</div>
  <div class="brand"><div class="mark"></div><span>Dr. Lena Hartwig-Brandt</span></div>
</section>

<!-- Workshop description -->
<section class="slide col-a row-3">
  <header class="header-band"><div class="dot"></div><h2>WORKSHOP DESCRIPTION</h2></header>
  <div class="desc-head">Resilience training for teachers:<br>Strengthening mental resilience in everyday teaching</div>
  <div class="desc-body">
    <p>Resilience describes the ability to cope with stress and crises while developing personally. Teachers face particular challenges in their daily work that test their mental strength. In this workshop, you will learn how to specifically promote your resilience and develop strategies for coping with stress in a healthy way.</p>
    <p>To achieve this, you will determine your personal resilience profile, reflect on your thought patterns, and recognize the connections between stressors, stress amplifiers, and stress reactions in the teaching context. You will develop resource-oriented courses of action and discuss their effectiveness. Furthermore, you will learn how social networks can strengthen your resilience and develop an individual transfer plan for practical implementation in your daily teaching practice.</p>
  </div>
  <div class="footer-date">03 &nbsp;|&nbsp; DATE: 11/01/2026</div>
  <div class="brand"><div class="mark"></div><span>Dr. Lena Hartwig-Brandt</span></div>
</section>

<!-- Working process -->
<section class="slide col-b row-3">
  <header class="header-band"><div class="dot"></div><h2>OUR WORKING PROCESS</h2></header>
  <div class="proc-text">
    <p class="lead">Resilience describes the ability to cope with stress and crises while developing personally. Teachers face particular challenges in their daily work that test their mental strength.</p>
    <p style="margin-top:7px">In this workshop, you will learn how to specifically promote your resilience and develop strategies for coping with stress in a healthy way. To achieve this, you will determine your personal resilience profile, reflect on your thought patterns, and recognize the connections between stressors, stress amplifiers, and stress reactions in the teaching context.</p>
    <p>You will develop resource-oriented courses of action and discuss their effectiveness. Furthermore, you will learn how social networks can strengthen.</p>
  </div>
  <ul class="bars">
    <li><div class="fill light" style="width:56%"></div><em>60%</em></li>
    <li><div class="fill dark" style="width:70%"></div><em>80%</em></li>
    <li><div class="fill light" style="width:42%"></div><em>40%</em></li>
    <li><div class="fill dark" style="width:33%"></div><em>30%</em></li>
    <li><div class="fill light" style="width:65%"></div><em>70%</em></li>
    <li><div class="fill dark" style="width:55%"></div><em>60%</em></li>
    <li><div class="fill light" style="width:78%"></div><em>70%</em></li>
  </ul>
  <div class="footer-date">07 &nbsp;|&nbsp; DATE: 11/01/2026</div>
  <div class="brand"><div class="mark"></div><span>Dr. Lena Hartwig-Brandt</span></div>
</section>

<!-- About -->
<section class="slide col-a row-4">
  <header class="header-band"><div class="dot"></div><h2>ABOUT LENA HARTWIG</h2></header>
  <div class="about-text">
    <p>Sed ut perspiciatis unde omnis iste natus error sit voluptatem accusantium doloremque laudantium, totam rem aperiam, eaque ipsa quae ab illo inventore veritatis et quasi architecto beatae vitae dicta sunt explicabo. Nemo enim ipsam voluptatem quia voluptas sit aspernatur</p>
    <p>Neque porro quisquam est, qui dolorem ipsum quia dolor sit amet, consectetur, adipisci velit.</p>
  </div>
  <div class="sig"><strong>DR. PHIL. LENA HARTWIG-BRANDT, MBA</strong><span>Expert in Didactics and Self-Leadership</span></div>
  <div class="portrait" role="img" aria-label="Round portrait photo of the trainer smiling at a laptop"></div>
  <div class="footer-date">04 &nbsp;|&nbsp; DATE: 11/01/2026</div>
  <div class="brand"><div class="mark"></div><span>Dr. Lena Hartwig-Brandt</span></div>
</section>

<!-- Closing -->
<section class="slide col-b row-4">
  <div class="close-photo" role="img" aria-label="Photo of colleagues in a relaxed group discussion"></div>
  <svg class="close-wave" viewBox="0 0 440 120" preserveAspectRatio="none" aria-hidden="true">
    <path d="M0 120 L0 38 C60 8 130 0 220 22 C300 42 380 46 440 18 L440 120 Z" fill="#ffffff"/>
    <path d="M0 120 L0 46 C60 18 130 12 220 34 C300 54 380 56 440 26 L440 120 Z" fill="#1a4a85"/>
  </svg>
  <div class="close-ring"></div>
  <div class="close-kicker">THANK YOU</div>
  <div class="close-title">FOR YOUR TIME, PARTICIPATION,<br>&amp; VALUABLE INSIGHTS.</div>
</section>

</body>
</html>
```